Natural cosmetics company is looking for a designer to produce the labels of the products and

Hello, Nus need a label and logo design for our brand RM ORGANIC. It is a brand specializing in the sale of 100% Natural cosmetic products on the internet. The first range is based on snail slime. I am looking for a clean design in green tones. The final design must be forwarded to the supplier for printing and shipping of the products. I realized a first idea for a logo, but I am interested in other ideas / suggestions. You have carte blanche :)
Here are the rules to follow for sending labels to the supplier:
• Sizes:
- Airless bottle: 10.3 x 5.5 cm
- Jar: 20x2.5cm
• Files must be in Corel Draw (. cdr) and / or vector PDF format
You must attach the file of the fonts used for the text in the label - We need this file as many fonts are difficult to find and we might need to move some text around for printing purposes
• The logo of your brand must be in a vector format along with all other components.
• Please do not add any borders or any cut marks to the design. We will do it on our end as we need to follow specific indications with our printing suppliers.
• All text and graphics must be at least 6mm from the edge
• The dimensions indicated by us must be respected in the overall size of the label
• The resolution to be used should be 300 cpi and in CMYK
• The text size should be readable and at least 4.5 points.

```html
<!DOCTYPE html>
<html lang="en">
<head>
<meta charset="utf-8">
<title>RM Organic – Snail Slime labels</title>
<link rel="stylesheet" href="https://fonts.googleapis.com/css2?family=Roboto+Slab:wght@300;500&family=Caveat+Brush&family=Herr+Von+Muellerhoff&display=swap">
<style>
  :root {
    --backdrop: #e4f0d6;
    --label: #ffffff;
    --ink: #2a2a2a;
    --green: #1f9a45;
    --green-soft: #7cc58d;
    --green-deep: #3f7a5a;
  }
  * { margin: 0; padding: 0; box-sizing: border-box; }
  html, body { width: 1200px; height: 486px; overflow: hidden; }
  body {
    position: relative;
    background: var(--backdrop);
    font-family: "Roboto Slab", Georgia, serif;
    color: var(--ink);
  }
  .label {
    position: absolute;
    background: var(--label);
  }
  .label--jar { left: 77px; top: 61px; width: 731px; height: 91px; }
  .label--bottle { left: 308px; top: 192px; width: 376px; height: 200px; }

  .copy {
    position: absolute;
    font-weight: 300;
    font-size: 7px;
    line-height: 1.12;
  }
  .copy strong { font-weight: 500; display: block; }
  .label--jar .copy--ingredients { left: 49px; top: 16px; width: 166px; }
  .label--jar .copy--directions { left: 544px; top: 20px; width: 152px; font-size: 6.2px; line-height: 1.05; }
  .label--bottle .copy--ingredients { left: 25px; top: 28px; width: 78px; }
  .label--bottle .copy--directions { left: 293px; top: 32px; width: 54px; font-size: 6.2px; line-height: 1.05; }

  .snail-art {
    position: absolute;
    border-radius: 60% 40% 45% 55% / 55% 60% 40% 45%;
    background: linear-gradient(160deg, var(--green-soft), var(--green) 70%);
  }
  .label--jar .snail-art { left: 256px; top: 30px; width: 90px; height: 38px; }
  .label--bottle .snail-art { left: 135px; top: 42px; width: 90px; height: 40px; }

  .brand-mark {
    position: absolute;
    width: 44px; height: 44px;
    border-radius: 50%;
    border: 1px solid var(--ink);
    background: var(--label);
    display: flex; align-items: center; justify-content: center;
    text-align: center;
    font-size: 7px; font-weight: 500; line-height: 1.1;
    color: var(--ink);
  }
  .label--jar .brand-mark { left: 287px; top: 17px; }
  .label--bottle .brand-mark { left: 168px; top: 28px; }

  .product-name {
    position: absolute;
    font-family: "Caveat Brush", cursive;
    color: var(--green);
    line-height: 1;
    white-space: nowrap;
    border-bottom: 2px solid var(--green);
  }
  .label--jar .product-name { left: 357px; top: 17px; font-size: 28px; padding-bottom: 1px; }
  .label--bottle .product-name { left: 121px; top: 88px; font-size: 36px; padding-bottom: 2px; }

  .tagline {
    position: absolute;
    font-family: "Herr Von Muellerhoff", cursive;
    color: var(--ink);
    white-space: nowrap;
    line-height: 1;
  }
  .label--jar .tagline { left: 349px; top: 58px; font-size: 15px; }
  .label--bottle .tagline { left: 116px; top: 148px; font-size: 18px; }

  .brand-logo {
    position: absolute;
    left: 45px; top: 217px;
    width: 204px; height: 204px;
    border-radius: 50%;
    background: var(--label);
    display: flex; align-items: center; justify-content: center;
    font-family: "Roboto Slab", Georgia, serif;
    font-weight: 500;
    font-size: 22px;
    color: var(--green-deep);
  }
</style>
</head>
<body>

  <section class="label label--jar" aria-label="Jar label">
    <p class="copy copy--ingredients"><strong>Natural active ingredients in slime</strong>Pure snail slime contains active ingredients beneficial to the skin: allantoin, collagen, glycolic acid, elastin, vitamin A and vitamin C, natural antibiotic peptides. It is these components that improve skin texture, help heal skin lesions and restore radiance to the complexion.</p>
    <div class="snail-art" role="img" aria-label="Green snail illustration"></div>
    <div class="brand-mark">RM<br>ORGANIC</div>
    <h2 class="product-name">Snail Slime</h2>
    <p class="tagline">100% Natural Cosmetic Product</p>
    <p class="copy copy--directions">Directions for use: apply a small amount of cream to clean, dry skin morning and evening. Massage gently in circular motions until fully absorbed. Avoid contact with eyes. For external use only. Store in a cool, dry place away from direct sunlight. Keep out of reach of children.</p>
  </section>

  <section class="label label--bottle" aria-label="Airless bottle label">
    <p class="copy copy--ingredients"><strong>Natural active ingredients in slime</strong>Pure snail slime contains active ingredients beneficial to the skin: allantoin, collagen, glycolic acid, elastin, vitamin A and vitamin C, natural antibiotic peptides. It is these components that improve skin texture, help heal skin lesions and restore radiance to the complexion.</p>
    <div class="snail-art" role="img" aria-label="Green snail illustration"></div>
    <div class="brand-mark">RM<br>ORGANIC</div>
    <h2 class="product-name">Snail Slime</h2>
    <p class="tagline">100% Natural Cosmetic Product</p>
    <p class="copy copy--directions">Directions: apply to clean, dry skin morning and evening. Massage gently until absorbed. Avoid contact with eyes. For external use only. Store in a cool, dry place. Keep out of reach of children.</p>
  </section>

  <div class="brand-logo">RM ORGANIC</div>

</body>
</html>
```